Medical consulting firm needs polished website

I am a physician and working on setting up a smal consulting firm in New Hampshire, USA. It is called Bright Harbor Medical Services, LLC and the website will be BrightHarborMed.com. I was puttering around at making my own website, and it just didn't come together nicely so I've decided to leave it to the pros. The focus of the business is Advanced Care Planning, ie planning for your future medical needs. So it deals with some heavy stuff like planning for if you get sick, who should make decisions for you, end of life options etc. So it can't be too flippant or cutesy, but also can't be too dour and dark. I am hoping to convey that by thinking ahead and making some plans you can lift some of the worries off of yourself and your family - and that we can help make a scary sounding path more manageable. I want it to be made with wordpress and I have actually already bought a template ( Vitarun – A Modern Multidisciplinary Medical & Health Theme ). The website needs to have general information about our services, doc profile, appointment maker, blog/url link page, and ideally web commerce application ( the template has access to woocommerce). I've posted my business card and current brochure (still tweaking them, but you get the idea). I am also partnering with lumenfold.com and so have included their logo and would want connections/info about them. I have the logos etc in different formats as needed.

Target Market(s)

middle aged to older adults

Industry/Entity Type

Medical

Coding

Coded - Design and coding required

Font styles to use
Sans Serif

Requirements
Must have
• as above.
Nice to have
• Ease of reading/access for elderly viewers. woo commerce.

```html
<!DOCTYPE html>
<html lang="en">
<head>
<meta charset="utf-8">
<title>Bright Harbor Medical Services</title>
<link href="https://fonts.googleapis.com/css2?family=Roboto:ital,wght@0,400;0,500;0,700;1,400&display=swap" rel="stylesheet">
<style>
:root{
  --blue:#2f86d6;
  --blue-light:#6bb8f5;
  --blue-dark:#1d6fb8;
  --navy:#1e4f86;
  --green:#4fd64a;
  --green-dark:#3ea83a;
  --ink:#222;
  --muted:#555;
  --white:#fff;
}
*{box-sizing:border-box;margin:0;padding:0}
html,body{width:674px;height:1200px;overflow:hidden;background:var(--white)}
body{font-family:"Roboto",Arial,sans-serif;color:var(--ink);position:relative}
.abs{position:absolute}

.topbar{left:0;top:0;width:674px;height:20px;background:linear-gradient(90deg,var(--blue),var(--blue-light));display:flex;justify-content:flex-end;align-items:center;gap:12px;padding-right:30px;font-size:8px;color:var(--white)}
.topbar span{display:flex;align-items:center;gap:3px}
.topbar .cta{background:var(--white);color:var(--ink);padding:2px 5px;border-radius:2px;font-weight:500}
.topbar svg{width:8px;height:8px}

.header{left:0;top:20px;width:674px;height:38px;background:var(--white)}
.brand{left:36px;top:6px;display:flex;align-items:center;gap:6px}
.brand-dot{width:14px;height:14px;border-radius:50%;background:var(--blue)}
.brand-name{font-size:12.5px;font-weight:500;color:var(--blue-dark);line-height:1.05;width:120px}
.nav{right:29px;top:14px;display:flex;gap:18px;font-size:8.6px;font-weight:500;color:var(--navy)}
.nav .active{color:var(--green-dark)}

.hero-photo{left:0;top:58px;width:674px;height:276px;
  background:
    radial-gradient(ellipse 95px 120px at 225px 150px,#e9c9b4 0,#e2c1ad 45%,rgba(226,193,173,0) 100%),
    radial-gradient(ellipse 110px 70px at 205px 85px,#eeeae6 0,rgba(238,234,230,0) 100%),
    radial-gradient(ellipse 160px 90px at 230px 280px,#cfd3d6 0,rgba(207,211,214,0) 100%),
    radial-gradient(ellipse 100px 120px at 470px 150px,#e3bfa6 0,#d9b39a 45%,rgba(217,179,154,0) 100%),
    radial-gradient(ellipse 120px 60px at 490px 75px,#d9d6d2 0,rgba(217,214,210,0) 100%),
    radial-gradient(ellipse 170px 90px at 520px 285px,#e9e8e6 0,rgba(233,232,230,0) 100%),
    linear-gradient(100deg,#d6dadc,#e9e6e2 45%,#d4c9bf)}
.hero-box{left:33px;top:298px;width:615px;height:70px;background:linear-gradient(90deg,var(--blue),var(--blue-light));color:var(--white);text-align:center;padding:12px 18px}
.hero-box h1{font-size:10px;font-weight:500;margin-bottom:9px}
.hero-box p{font-size:7px;line-height:1.55}

.section-title{left:0;width:674px;text-align:center;font-size:12.5px;font-weight:500;color:var(--ink)}
.section-title span{color:var(--blue-dark)}
.dotted{left:30px;width:615px;border-top:1px dotted var(--blue)}

.service{top:430px;width:142px;height:82px}
.service .photo{position:absolute;inset:0 0 12px 0}
.p1{background:radial-gradient(ellipse 40px 35px at 105px 30px,#c8733f,rgba(200,115,63,0)),radial-gradient(ellipse 45px 40px at 40px 45px,#e7c4ad,rgba(231,196,173,0)),linear-gradient(90deg,#f2ece7,#e8d2c2)}
.p2{background:radial-gradient(ellipse 50px 30px at 90px 50px,#2d3440,rgba(45,52,64,0)),radial-gradient(ellipse 50px 40px at 40px 30px,#f2f4f6,rgba(242,244,246,0)),linear-gradient(90deg,#c9ced4,#9aa3ad)}
.p3{background:radial-gradient(ellipse 50px 35px at 60px 45px,#f1f2f4,rgba(241,242,244,0)),linear-gradient(90deg,#5d8fc9,#3f76b6 60%,#6a9ad0)}
.p4{background:radial-gradient(ellipse 35px 35px at 30px 40px,#c9a58a,rgba(201,165,138,0)),radial-gradient(ellipse 40px 40px at 110px 40px,#5f5148,rgba(95,81,72,0)),linear-gradient(90deg,#e7e1d8,#d7cfc4)}
.service .icon{position:absolute;left:58px;top:-14px;width:26px;height:26px;border-radius:50%;background:var(--blue);border:2px solid var(--white);display:flex;align-items:center;justify-content:center}
.service .icon svg{width:12px;height:12px}
.service .label{position:absolute;left:6px;right:6px;bottom:0;height:24px;background:linear-gradient(90deg,var(--blue),var(--blue-light));color:var(--white);font-size:8px;font-weight:500;display:flex;align-items:center;justify-content:center;border-radius:2px}

.about{left:0;top:526px;width:337px;height:214px;background:linear-gradient(135deg,var(--blue-dark),var(--blue-light));color:var(--white);text-align:center;padding:14px 28px}
.about h2,.mail h2{font-size:15px;font-weight:500;margin-bottom:12px}
.about p{font-size:8px;line-height:1.6;margin-bottom:9px}
.btn-outline{display:inline-block;border:1px solid var(--white);font-size:7px;font-weight:500;padding:5px 10px;margin-top:2px;border-radius:2px}
.mail{left:337px;top:526px;width:337px;height:214px;background:var(--green);color:var(--white);text-align:center;padding:14px 28px 0 28px}
.field{position:absolute;background:var(--white);font-size:7px;color:#999;padding:4px 6px;text-align:left;border-radius:1px}
.send{position:absolute;left:130px;top:179px;width:76px;height:18px;background:var(--white);color:var(--ink);font-size:7px;font-weight:500;display:flex;align-items:center;justify-content:center;border-radius:2px}

.quote{width:230px;font-size:7px;line-height:1.6}
.quote p{font-style:italic;color:var(--muted)}
.quote .who{font-style:normal;color:var(--ink);margin-top:7px}
.quote.left{text-align:right}
.avatar{width:43px;height:43px;border-radius:50%}
.a1{background:radial-gradient(circle at 50% 42%,#e2b596 0,#d3a283 30%,#f1f1f1 55%,#e2e2e2)}
.a2{background:radial-gradient(circle at 50% 42%,#e3b79a 0,#c89066 30%,#9b6a3e 55%,#2f2a27)}
.a3{background:radial-gradient(circle at 50% 42%,#e7c1a8 0,#d9ab8f 28%,#4a3a31 52%,#cfcbc7)}
.a4{background:radial-gradient(circle at 50% 45%,#d8a98a 0,#c39276 28%,#3a2d26 52%,#ececec)}
.divider-v{left:337px;top:800px;height:122px;border-left:1px dotted var(--blue)}

.skyline{left:0;top:928px;width:674px;height:36px;background:linear-gradient(180deg,#fff 0,#cfe4f6 45%,var(--blue) 100%)}
.footer{left:0;top:964px;width:674px;height:236px;background:linear-gradient(135deg,var(--blue),var(--blue-light));color:var(--white)}
.footer h3{font-size:10px;font-weight:500;margin-bottom:12px}
.footer p{font-size:7px;line-height:1.6;margin-bottom:7px}
.socials{display:flex;gap:8px;margin-top:4px}
.socials span{width:7px;height:7px;border-radius:50%;background:var(--white)}
.map{left:187px;top:51px;width:300px;height:118px;
  background:
    radial-gradient(ellipse 60px 130px at 20px 70px,#a9cdea,rgba(169,205,234,0)),
    radial-gradient(ellipse 80px 60px at 290px 110px,#a9cdea,rgba(169,205,234,0)),
    radial-gradient(ellipse 90px 60px at 170px 55px,#f3ead7,rgba(243,234,215,0)),
    linear-gradient(135deg,#e8e4d8,#dfe6dc 50%,#e7e2d4)}
.post{display:flex;gap:9px;margin-bottom:14px}
.post .thumb{width:26px;height:26px;border-radius:50%;flex:none}
.t1{background:radial-gradient(circle at 40% 40%,#c79a72,#3a2f28)}
.t2{background:radial-gradient(circle at 40% 40%,#d9d2c8,#6b5a4b)}
.t3{background:radial-gradient(circle at 40% 40%,#c08a5a,#4a3424)}
.post .t{font-size:7.5px}
.post .m{font-size:6px;opacity:.85;margin-top:2px}
.foot-line{left:29px;top:199px;width:616px;border-top:1px solid rgba(255,255,255,.6)}
.copy{left:0;top:214px;width:674px;text-align:center;font-size:7px}
</style>
</head>
<body>

<div class="abs topbar">
  <span><svg viewBox="0 0 10 10"><path d="M2 1l2 2-1 1.5a6 6 0 0 0 2.5 2.5L7 6l2 2-1.5 1.5C4 9 1 6 .5 2z" fill="#fff"/></svg>+1 603 555 01 42</span>
  <span><svg viewBox="0 0 10 10"><rect x="0" y="2" width="10" height="6" fill="#fff"/></svg>info@brightharbormed.com</span>
  <span class="cta">Make an appointment</span>
  <svg viewBox="0 0 10 10"><circle cx="4" cy="4" r="3" fill="none" stroke="#fff" stroke-width="1.4"/><path d="M6.2 6.2L9 9" stroke="#fff" stroke-width="1.4"/></svg>
</div>

<header class="abs header">
  <div class="abs brand">
    <span class="brand-dot"></span>
    <span class="brand-name">Bright Harbor Medical Services</span>
  </div>
  <nav class="abs nav">
    <span class="active">HOME</span><span>ABOUT US</span><span>OUR SERVICES</span><span>TEAM</span><span>BLOG</span><span>SHOP</span><span>CONTACT US</span>
  </nav>
</header>

<div class="abs hero-photo" role="img" aria-label="Photo of a smiling older couple facing each other"></div>
<div class="abs hero-box">
  <h1>Bright Harbor Medical Services, LLC</h1>
  <p>Advanced Care Planning helps your voice to always be heard. None of us like to think about getting sick, injured, or even dying but.. unfortunately wishful thinking doesn't protect us, but making a plane can help. We are here to help you arieve the peace of mind that comes from taking charge!</p>
</div>

<h2 class="abs section-title" style="top:374px">Our <span>Services</span></h2>
<div class="abs dotted" style="top:396px"></div>

<div class="abs service" style="left:29px">
  <div class="photo p1" role="img" aria-label="Photo of a physician examining a patient"></div>
  <div class="icon"><svg viewBox="0 0 12 12"><path d="M3 2h6v4a3 3 0 0 1-6 0z" fill="#fff"/></svg></div>
  <div class="label">Individualized Physician</div>
</div>
<div class="abs service" style="left:186px">
  <div class="photo p2" role="img" aria-label="Photo of a doctor consulting with a patient"></div>
  <div class="icon"><svg viewBox="0 0 12 12"><circle cx="6" cy="6" r="2" fill="#fff"/><circle cx="2" cy="3" r="1.3" fill="#fff"/><circle cx="10" cy="3" r="1.3" fill="#fff"/><circle cx="2" cy="9" r="1.3" fill="#fff"/><circle cx="10" cy="9" r="1.3" fill="#fff"/></svg></div>
  <div class="label">Complex Medical Situations</div>
</div>
<div class="abs service" style="left:344px">
  <div class="photo p3" role="img" aria-label="Photo of a clinician writing on a form"></div>
  <div class="icon"><svg viewBox="0 0 12 12"><path d="M3 1h4l2 2v8H3z" fill="#fff"/></svg></div>
  <div class="label">Advanced Directives</div>
</div>
<div class="abs service" style="left:502px">
  <div class="photo p4" role="img" aria-label="Photo of a family meeting with a doctor"></div>
  <div class="icon"><svg viewBox="0 0 12 12"><circle cx="6" cy="6" r="5" fill="#fff"/><text x="6" y="8.5" font-size="7" text-anchor="middle" fill="#2f86d6" font-family="Roboto,sans-serif">?</text></svg></div>
  <div class="label">Sharing your Decisions</div>
</div>

<section class="abs about">
  <h2>About Us</h2>
  <p>Advanced Directives are legally binding documents that spell out what type of medical care would - or would not - want done to you.</p>
  <p>We often assume that our families or medical professionals will make "The right decision", but this can be an anguishing process - and often does not accurately reflects the patient's true desires.</p>
  <p>By making your choices clear, your family and caregivers can honor your wishes when you cannot speak for yourself</p>
  <span class="btn-outline">LEARN MORE</span>
</section>

<section class="abs mail">
  <h2>Feel Free to Mail</h2>
  <div class="field" style="left:28px;top:45px;width:136px">Name *</div>
  <div class="field" style="left:174px;top:45px;width:135px">Email *</div>
  <div class="field" style="left:28px;top:74px;width:281px">Subject</div>
  <div class="field" style="left:28px;top:103px;width:281px;height:64px">Write Your Message Here...</div>
  <div class="send">SEND MESSAGE</div>
</section>

<h2 class="abs section-title" style="top:744px">What <span>People Say</span></h2>
<div class="abs dotted" style="top:766px"></div>

<div class="abs quote left" style="left:30px;top:798px">
  <p>At vero eos et accusamus et iusto odio dignissimos ducimus qui blanditiis praesentium voluptatum deleniti atque corrupti quos dolores et quas molestias excepturi sint occaecati.</p>
  <div class="who">Owen Pratt , Developer</div>
</div>
<div class="abs avatar a1" style="left:275px;top:799px" role="img" aria-label="Portrait of a client"></div>

<div class="abs avatar a2" style="left:355px;top:799px" role="img" aria-label="Portrait of a client"></div>
<div class="abs quote" style="left:415px;top:798px">
  <p>Luis aute irure dolor in reprehenderit in piluptate velit esse cillum dolore eu fugiat nulla pariatur. Excepteur sint occaecat cupidatat non proident, sunt in culpa qui officia deserunt mollit.</p>
  <div class="who">Nora Hale , Manager</div>
</div>

<div class="abs dotted" style="top:861px"></div>
<div class="abs divider-v"></div>

<div class="abs quote left" style="left:30px;top:876px">
  <p>Provident, similique sunt in culpa qui officia deserunt mollitia animi, id est laborum et dolorum fuga. Et harum quidem rerum facilis est et expedita distinctio. Nam libero tempore, cum soluta nobis.</p>
  <div class="who">Elise Marsh , Creative Designer</div>
</div>
<div class="abs avatar a3" style="left:275px;top:877px" role="img" aria-label="Portrait of a client"></div>

<div class="abs avatar a4" style="left:355px;top:877px" role="img" aria-label="Portrait of a client"></div>
<div class="abs quote" style="left:415px;top:876px">
  <p>Duis aute irure dolor in reprehenderit in voluptate velit esse cillum dolore eu fugiat nulla pariatur. Excepteur sint occaecat cupidatat non proident, sunt in culpa qui officia deserunt mollit.</p>
  <div class="who">Carl Benning , Operations Manager</div>
</div>

<div class="abs skyline" role="img" aria-label="City skyline and airport silhouette"></div>

<footer class="abs footer">
  <div class="abs" style="left:29px;top:26px;width:140px">
    <h3>Contact Us</h3>
    <p>Maecenas etos sit amet, consectetur adipiscing elit. Terminal volutpat rutrum metro amet sollicitudin interdum.</p>
    <p><b style="font-weight:500">Phone:</b> +1 (800) 555 01 96</p>
    <p><b style="font-weight:500">Office:</b> 214 Linden Row, Concord</p>
    <p><b style="font-weight:500">Email:</b> hello@brightharbormed.com</p>
    <div class="socials"><span></span><span></span><span></span><span></span><span></span></div>
  </div>
  <h3 class="abs" style="left:187px;top:26px;width:300px;text-align:center">Headquarters</h3>
  <div class="abs map" role="img" aria-label="Street map showing the headquarters location"></div>
  <div class="abs" style="left:503px;top:26px;width:150px">
    <h3>Recent Posts</h3>
    <div class="post"><span class="thumb t1"></span><div><div class="t">Business Cards Design Trends</div><div class="m">Dec 02, 2020 / 2 comments</div></div></div>
    <div class="post"><span class="thumb t2"></span><div><div class="t">This Maravelous App</div><div class="m">Nov 18, 2020 / 9 comments</div></div></div>
    <div class="post"><span class="thumb t3"></span><div><div class="t">Brand Paper Niceties</div><div class="m">Nov 10, 2020 / 0 comments</div></div></div>
  </div>
  <div class="abs foot-line"></div>
  <div class="abs copy">Copyright 2020. All Rights Reserved by Company Name</div>
</footer>

</body>
</html>
```